Corvel Capital LLC

Need Professional Business cards for New Investment Fund

Target Market(s)

High Quality investors

Industry/Entity Type

Financial

Contact Information for Business Card

Phone Number +1 555 284 6190
Name Lukas Varenko
Title Fund Manager
email lv@FundCorvel.com
Website www.FundCorvel.com

Colors

Designer to choose colors to be used in the design.

Requirements
Must have
• Must have our Logo and all of the above. Must be made so lettering and loge can be raised

```html
<!DOCTYPE html>
<html lang="en">
<head>
<meta charset="utf-8">
<title>Vantrelo Capital – Business Card</title>
<link rel="stylesheet" href="https://fonts.googleapis.com/css2?family=Montserrat:wght@300;400;600&display=swap">
<style>
  :root {
    --forest: #434c41;
    --leaf: #5bbb47;
    --paper: #ffffff;
    --ink: #434c41;
  }
  html, body {
    margin: 0;
    padding: 0;
    width: 1200px;
    height: 720px;
    overflow: hidden;
    background: var(--paper);
  }
  .card {
    position: relative;
    width: 1200px;
    height: 720px;
    background: var(--paper);
    font-family: "Montserrat", sans-serif;
    overflow: hidden;
  }
  .card__shapes {
    position: absolute;
    inset: 0;
  }
  .shape--top { fill: var(--forest); }
  .shape--bottom { fill: var(--leaf); }

  .holder {
    position: absolute;
    right: 224px;
    top: 128px;
    text-align: right;
    color: var(--paper);
  }
  .holder__name {
    margin: 0;
    font-size: 40px;
    font-weight: 600;
    letter-spacing: 0.3px;
    line-height: 1.1;
  }
  .holder__title {
    margin: 4px 0 0;
    font-size: 31px;
    font-weight: 300;
    letter-spacing: 0.4px;
    line-height: 1.2;
  }

  .brand {
    position: absolute;
    left: 150px;
    top: 436px;
    display: flex;
    align-items: center;
    gap: 16px;
  }
  .brand__square {
    width: 38px;
    height: 38px;
    background: var(--leaf);
  }
  .brand__name {
    font-size: 42px;
    font-weight: 600;
    color: var(--ink);
    letter-spacing: 0.5px;
  }
  .brand-mini {
    position: absolute;
    left: 1024px;
    top: 390px;
    width: 38px;
    height: 38px;
    background: var(--leaf);
  }

  .contacts {
    position: absolute;
    left: 530px;
    top: 420px;
    margin: 0;
    padding: 0;
    list-style: none;
    color: var(--ink);
  }
  .contacts__item {
    display: flex;
    align-items: center;
    height: 43px;
    font-size: 34px;
    font-weight: 300;
    letter-spacing: 0.3px;
  }
  .contacts__icon {
    width: 26px;
    height: 26px;
    margin-right: 20px;
    fill: var(--ink);
  }
</style>
</head>
<body>
  <main class="card">
    <svg class="card__shapes" width="1200" height="720" viewBox="0 0 1200 720" aria-hidden="true">
      <polygon class="shape--top" points="165,0 1200,0 1200,256 549,256 549,363"/>
      <polygon class="shape--bottom" points="371,576 1024,576 1024,469 1200,640 1200,720 270,720"/>
    </svg>

    <header class="holder">
      <h1 class="holder__name">Lukas Varenko</h1>
      <p class="holder__title">Fund Manager</p>
    </header>

    <div class="brand">
      <span class="brand__square"></span>
      <span class="brand__name">VANTRELO</span>
    </div>
    <span class="brand-mini"></span>

    <ul class="contacts">
      <li class="contacts__item">
        <svg class="contacts__icon" viewBox="0 0 24 24" aria-hidden="true">
          <path d="M6.6 10.8a15.1 15.1 0 0 0 6.6 6.6l2.2-2.2a1 1 0 0 1 1-.25 11.4 11.4 0 0 0 3.6.57 1 1 0 0 1 1 1V20a1 1 0 0 1-1 1A17 17 0 0 1 3 4a1 1 0 0 1 1-1h3.5a1 1 0 0 1 1 1c0 1.25.2 2.45.57 3.6a1 1 0 0 1-.25 1z"/>
        </svg>
        +1 555 284 6190
      </li>
      <li class="contacts__item">
        <svg class="contacts__icon" viewBox="0 0 24 24" aria-hidden="true">
          <path d="M2 9l10-6 10 6v11H2zM4 9.6l8 5 8-5-8-4.8z"/>
        </svg>
        lv@FundCorvel.com
      </li>
      <li class="contacts__item">
        <svg class="contacts__icon" viewBox="0 0 24 24" aria-hidden="true">
          <path d="M12 2a10 10 0 1 0 0 20 10 10 0 0 0 0-20zm7.9 9h-3.4a15 15 0 0 0-1.3-6.2A8 8 0 0 1 19.9 11zM12 4c.9 1.1 2.3 3.6 2.5 7h-5C9.7 7.6 11.1 5.1 12 4zM8.8 4.8A15 15 0 0 0 7.5 11H4.1a8 8 0 0 1 4.7-6.2zM4.1 13h3.4a15 15 0 0 0 1.3 6.2A8 8 0 0 1 4.1 13zM12 20c-.9-1.1-2.3-3.6-2.5-7h5c-.2 3.4-1.6 5.9-2.5 7zm3.2-.8a15 15 0 0 0 1.3-6.2h3.4a8 8 0 0 1-4.7 6.2z"/>
        </svg>
        www.FundCorvel.com
      </li>
    </ul>
  </main>
</body>
</html>
```